Label design for our new range of organic honey.

We need a design for honey jars and tubs. The label needs to indicate we are located in the Western Australia. The design needs to be elegant, modern and attracting high end customers that focus on quality.

Need extra days to review

```html
<!DOCTYPE html>
<html lang="en">
<head>
<meta charset="utf-8">
<title>Organic Honey – Label Range</title>
<link href="https://fonts.googleapis.com/css2?family=DM+Serif+Display&family=Young+Serif&family=Lora:ital@1&display=swap" rel="stylesheet">
<style>
  :root {
    --backdrop: #ebebe9;
    --label-charcoal: #3d3d3d;
    --map-tone: #5a5a5a;
    --ink-white: #ffffff;
    --gold-deep: #8a7444;
    --gold-light: #efe2b2;
  }
  html, body {
    margin: 0;
    padding: 0;
    width: 1200px;
    height: 1200px;
    overflow: hidden;
    background: var(--backdrop);
  }
  .label-range {
    position: relative;
    width: 1200px;
    height: 1200px;
  }
  .label {
    position: absolute;
    display: block;
    overflow: hidden;
  }
  .label--hexagon { left: 59px; top: 450px; }
  .label--framed-band { left: 417px; top: 448px; }
  .label--full-band { left: 804px; top: 461px; }

  .label-shape { fill: var(--label-charcoal); }
  .label-band { fill: var(--label-charcoal); }
  .map-area { opacity: 0.55; }
  .gold-frame { fill: none; stroke: url(#gold-sheen); stroke-width: 2.2; stroke-linejoin: round; }

  .word-organic {
    font-family: "Young Serif", serif;
    font-size: 21px;
    fill: var(--ink-white);
  }
  .word-honey {
    font-family: "DM Serif Display", serif;
    font-size: 48px;
    letter-spacing: 0.5px;
    fill: url(#gold-sheen);
  }
  .word-purity {
    font-family: "Young Serif", serif;
    font-size: 13px;
    fill: var(--ink-white);
  }
  .origin-line {
    font-family: "Lora", serif;
    font-style: italic;
    font-size: 11px;
    fill: var(--ink-white);
  }
  .gold-rule { fill: url(#gold-sheen); }
  .brand-name {
    font-family: "Young Serif", serif;
    font-size: 6.4px;
    letter-spacing: 1.2px;
    fill: var(--ink-white);
  }
  .brand-dot { fill: none; stroke: var(--ink-white); stroke-width: 1; }
</style>
</head>
<body>
<main class="label-range">

  <svg width="0" height="0" style="position:absolute" aria-hidden="true">
    <defs>
      <linearGradient id="gold-sheen" x1="0" y1="0" x2="1" y2="0">
        <stop offset="0" stop-color="#8a7444"/>
        <stop offset="0.3" stop-color="#d8c48c"/>
        <stop offset="0.55" stop-color="#9e8650"/>
        <stop offset="0.8" stop-color="#efe2b2"/>
        <stop offset="1" stop-color="#a28a55"/>
      </linearGradient>
      <radialGradient id="map-glow" cx="0.5" cy="0.5" r="0.6">
        <stop offset="0" stop-color="#5e5e5e"/>
        <stop offset="1" stop-color="#444444"/>
      </radialGradient>
      <clipPath id="hexagon-sticker-clip">
        <polygon points="86,4 226,4 308,143 226,282 86,282 4,143"/>
      </clipPath>
      <clipPath id="framed-hexagon-clip">
        <polygon points="97,4 264,4 324,145 264,286 97,286 37,145"/>
      </clipPath>
      <clipPath id="full-band-clip">
        <rect x="0" y="0" width="354" height="278"/>
      </clipPath>
    </defs>
  </svg>

  <!-- Variant 1: hexagon sticker -->
  <svg class="label label--hexagon" width="312" height="286" viewBox="0 0 312 286">
    <polygon class="label-shape" points="86,4 226,4 308,143 226,282 86,282 4,143"
             stroke="var(--label-charcoal)" stroke-width="8" stroke-linejoin="round"/>
    <g clip-path="url(#hexagon-sticker-clip)">
      <rect class="map-area" x="42" y="30" width="262" height="235" rx="40" fill="url(#map-glow)"
            role="img" aria-label="Outline map of Australia"/>
    </g>
    <g class="brand-mark">
      <circle class="brand-dot" cx="44" cy="149" r="4"/>
      <text class="brand-name" x="52" y="146">SALTBUSH</text>
      <text class="brand-name" x="52" y="155">RIDGE HONEY</text>
    </g>
    <text class="word-organic" x="210" y="118" text-anchor="middle">organic</text>
    <text class="word-honey" x="204" y="167" text-anchor="middle">HONEY</text>
    <text class="word-purity" x="210" y="186" text-anchor="middle">100% Pure</text>
    <text class="origin-line" x="127" y="227" text-anchor="middle">from</text>
    <text class="origin-line" x="147" y="240" text-anchor="middle">Western Australia</text>
    <rect class="gold-rule" x="92" y="251" width="107" height="4"/>
  </svg>

  <!-- Variant 2: band with framed hexagon -->
  <svg class="label label--framed-band" width="356" height="290" viewBox="0 0 356 290">
    <rect class="label-band" x="0" y="25" width="356" height="241"/>
    <polygon class="label-shape" points="97,4 264,4 324,145 264,286 97,286 37,145"
             stroke="var(--label-charcoal)" stroke-width="8" stroke-linejoin="round"/>
    <g clip-path="url(#framed-hexagon-clip)">
      <rect class="map-area" x="58" y="40" width="262" height="205" rx="40" fill="url(#map-glow)"
            role="img" aria-label="Outline map of Australia"/>
    </g>
    <polygon class="gold-frame" points="104,16 257,16 311,145 257,274 104,274 50,145"/>
    <g class="brand-mark">
      <circle class="brand-dot" cx="73" cy="157" r="4"/>
      <text class="brand-name" x="81" y="154">SALTBUSH</text>
      <text class="brand-name" x="81" y="163">RIDGE HONEY</text>
    </g>
    <text class="word-organic" x="230" y="126" text-anchor="middle">organic</text>
    <text class="word-honey" x="226" y="172" text-anchor="middle">HONEY</text>
    <text class="word-purity" x="230" y="190" text-anchor="middle">100% Pure</text>
    <text class="origin-line" x="154" y="226" text-anchor="middle">from</text>
    <text class="origin-line" x="171" y="239" text-anchor="middle">Western Australia</text>
    <rect class="gold-rule" x="121" y="250" width="98" height="4"/>
  </svg>

  <!-- Variant 3: full wrap band -->
  <svg class="label label--full-band" width="354" height="278" viewBox="0 0 354 278">
    <rect class="label-band" x="0" y="0" width="354" height="278"/>
    <g clip-path="url(#full-band-clip)">
      <rect class="map-area" x="50" y="18" width="280" height="250" rx="44" fill="url(#map-glow)"
            role="img" aria-label="Outline map of Australia with Tasmania"/>
    </g>
    <g class="brand-mark">
      <circle class="brand-dot" cx="71" cy="132" r="4"/>
      <text class="brand-name" x="79" y="129">SALTBUSH</text>
      <text class="brand-name" x="79" y="138">RIDGE HONEY</text>
    </g>
    <text class="word-organic" x="228" y="108" text-anchor="middle">organic</text>
    <text class="word-honey" x="224" y="153" text-anchor="middle">HONEY</text>
    <text class="word-purity" x="228" y="170" text-anchor="middle">100% Pure</text>
    <text class="origin-line" x="152" y="203" text-anchor="middle">from</text>
    <text class="origin-line" x="169" y="216" text-anchor="middle">Western Australia</text>
    <rect class="gold-rule" x="119" y="226" width="98" height="4"/>
  </svg>

</main>
</body>
</html>
```